RV7 - Rapid Vigil Field Operations Suite

I need an introductory website for RV7 which describes the features of the product and the ease of use of the product. The product is focused on Preparing for an incident using Volunteer and Resource management and then responding to an incident with Incident Management, Team Management, Task Management and Communication Management. Once a situation is handled, the application provides complete reporting on each of the above aspects

Target Market(s)

Local Government entities, specifically the emergency department directors or coordinators

Industry/Entity Type

Government Office

Coding

Coded - Design and coding required

Font styles to use
Sans Serif

Requirements
Must have
• Clear layout with modern images. I want to be able to get a clear understanding of the features of the product and the ease of use. I would like to high light how the application helps in Communication Management, Team Management, Task Management and Incident Managements. Also, how the use of application helps to get an immediate snap shot of how well an incident was handled. I want to highlight how the Dashboard provides a quick look at the Incident(s) being managed
Nice to have
• I would like to in the future add videos to the site. At this point don't have any ideas about nice to have features
Should not have
• traditional designs. I am looking for a slick, modern looking website. Clean design is the key.

```html
<!DOCTYPE html>
<html lang="en">
<head>
<meta charset="utf-8">
<title>RV7 - Rapid Vigil Field Operations Suite</title>
<link href="https://fonts.googleapis.com/css2?family=Lato:ital,wght@0,400;0,700;0,900;1,400&display=swap" rel="stylesheet">
<style>
:root{
  --green:#7aa32b;
  --green-dark:#6a8f22;
  --blue:#1565c0;
  --blue-deep:#0d4a94;
  --app-blue:#1976d2;
  --ink:#222;
  --text:#555;
  --muted:#888;
  --line:#ddd;
  --soft:#f3f3f3;
  --white:#fff;
}
*{box-sizing:border-box;margin:0;padding:0}
html,body{width:1200px;height:2862px;overflow:hidden}
body{font-family:"Lato",Arial,sans-serif;color:var(--ink);background:var(--white);position:relative}
.abs{position:absolute}

/* header */
.site-header{position:absolute;top:0;left:0;width:1200px;height:143px;background:var(--white)}
.brand{position:absolute;left:76px;top:28px;display:flex;align-items:center;gap:20px}
.brand-mark{width:76px;height:76px;border-radius:50%;background:var(--blue)}
.brand-name{font-size:32px;font-weight:700;color:#1f2a44;line-height:1}
.brand-tag{font-size:15px;color:#333;margin-top:6px;width:230px;line-height:1.3}
.login{position:absolute;left:998px;top:29px;width:74px;height:32px;border-radius:16px;background:var(--green);color:#fff;font-size:12px;font-weight:700;display:flex;align-items:center;justify-content:center}
.search{position:absolute;left:1091px;top:29px;width:32px;height:32px;border-radius:50%;background:#e6e6e6}
.main-nav{position:absolute;top:86px;left:523px;display:flex;align-items:center;font-size:13px;color:#333;letter-spacing:.3px}
.main-nav span{margin-right:42px}
.main-nav .active{border:2px solid var(--green);border-radius:18px;padding:7px 16px;color:var(--green);margin-right:36px}

/* hero */
.hero{position:absolute;top:143px;left:0;width:1200px;height:502px;background:linear-gradient(100deg,#d8d4cc 0%,#8c8174 35%,#4a4038 60%,#6d6a66 100%)}
.hero h1{position:absolute;top:200px;left:0;width:1200px;text-align:center;color:#fff;font-style:italic;font-weight:400;font-size:42px;line-height:58px}
.dots{position:absolute;top:452px;left:562px;display:flex;gap:8px}
.dots i{width:14px;height:14px;border-radius:50%;background:#fff;display:block}
.dots i:first-child{background:transparent;border:2px solid #fff}

/* features */
.intro{position:absolute;top:718px;left:200px;width:800px;text-align:center;font-style:italic;font-size:20px;line-height:32px;color:#333}
.feature-band{position:absolute;top:940px;left:0;width:1200px;height:250px;background:linear-gradient(#efefef,#fafafa)}
.feature{position:absolute;top:836px;width:230px;text-align:center}
.feature .photo{width:230px;height:230px;border-radius:50%;border:8px solid #fff;box-shadow:0 2px 8px rgba(0,0,0,.2)}
.feature h3{margin-top:22px;font-size:17px;font-weight:400;line-height:22px;color:#222}

/* application */
.app-section{position:absolute;top:1190px;left:0;width:1200px;height:546px;background:var(--white)}
.section-title{font-size:26px;font-weight:700;color:var(--green)}
.app-copy{position:absolute;left:76px;top:95px;width:240px}
.app-copy p{font-size:13.5px;line-height:24px;color:var(--text);margin-top:22px}
.btn{display:inline-flex;align-items:center;justify-content:center;width:126px;height:40px;border-radius:20px;background:var(--green);color:#fff;font-size:13px}
.app-copy .btn{margin-top:28px}
.phone{position:absolute;top:75px;width:229px;height:410px;background:#f2f2f2;overflow:hidden;font-size:11px}
.status{height:14px;background:#0d47a1}
.appbar{height:36px;background:var(--app-blue);color:#fff;font-weight:700;display:flex;align-items:center;padding-left:40px;font-size:12px}
.drawer{position:absolute;top:14px;left:0;width:180px;height:396px;background:var(--app-blue);color:#fff}
.drawer-shade{position:absolute;top:14px;left:180px;width:49px;height:396px;background:#5a6a7a}
.drawer .avatar{width:34px;height:34px;border-radius:50%;background:#f5c542;margin:14px 0 4px 14px}
.drawer .who{padding-left:14px;font-weight:700;font-size:12px}
.drawer .role{padding-left:14px;font-size:10px;opacity:.8;margin-bottom:12px}
.drawer li{list-style:none;padding:8px 0 8px 44px;font-size:10px}
.drawer li.on{background:#1565c0}
.card{background:#fff;margin:10px 10px 0;border-top:3px solid #1565c0;box-shadow:0 1px 3px rgba(0,0,0,.2);padding:6px 8px;color:#666;font-size:10px;line-height:14px}
.card b{display:block;color:#555;font-weight:400;font-size:11px}
.card .time{color:#d32f2f;font-size:17px;margin-top:4px}
.card .date{text-align:right;font-size:9px;color:#777}

/* why */
.why{position:absolute;top:1736px;left:0;width:1200px;height:454px;background:var(--soft)}
.why h2{position:absolute;left:76px;top:60px;font-size:25px;font-weight:700;color:#222}
.why ul{position:absolute;left:76px;top:116px;width:460px;list-style:none}
.why li{position:relative;padding-left:33px;font-size:13.5px;line-height:21px;color:#444;margin-bottom:12px}
.why li::before{content:"";position:absolute;left:0;top:3px;width:15px;height:15px;border-radius:50%;background:var(--green)}
.why .btn{position:absolute;left:76px;top:355px}
.why-art{position:absolute;top:0;left:0}

/* partners */
.partners{position:absolute;top:2190px;left:0;width:1200px;height:226px}
.partners h4{position:absolute;top:68px;width:1200px;text-align:center;font-size:16px;font-weight:400;letter-spacing:1.5px;color:#333}
.partner{position:absolute;top:128px;display:flex;align-items:center;gap:8px;font-size:22px;font-weight:700;color:#555;transform:translateX(-50%)}
.partner i{width:22px;height:22px;border-radius:50%;background:#bbb;display:block}

/* footer */
.site-footer{position:absolute;top:2416px;left:0;width:1200px;height:446px;background:linear-gradient(#1a63b0,#0c4791);color:#fff}
.foot-mark{position:absolute;left:76px;top:62px;width:72px;height:72px;border-radius:50%;border:3px solid rgba(255,255,255,.8)}
.foot-about{position:absolute;left:76px;top:154px;width:250px;font-style:italic;font-size:12.5px;line-height:24px}
.btn-ghost{position:absolute;left:76px;top:245px;width:120px;height:36px;border:2px solid #fff;border-radius:18px;font-size:12px;display:flex;align-items:center;justify-content:center}
.col{position:absolute;top:66px}
.col h5{font-size:17px;font-weight:700;letter-spacing:.3px;margin-bottom:24px}
.links li{list-style:none;font-size:13px;height:33px;position:relative;padding-left:28px}
.links li::before{content:"";position:absolute;left:0;top:1px;width:13px;height:13px;border:2px solid #fff;border-radius:50%}
.social li{list-style:none;font-size:13px;height:48px;position:relative;padding-left:28px}
.social li::before{content:"";position:absolute;left:0;top:1px;width:14px;height:14px;background:#fff;border-radius:2px}
.field{width:233px;height:38px;border-radius:19px;background:#2c73bf;font-style:italic;font-size:12px;padding:12px 24px;margin-bottom:14px}
.send{width:233px;height:38px;border-radius:19px;background:var(--green);font-size:13px;font-weight:700;display:flex;align-items:center;justify-content:center;margin-top:6px}
.copyright{position:absolute;left:0;top:392px;width:1200px;text-align:center;font-size:12px}
.foot-rule{position:absolute;left:0;top:366px;width:1200px;height:1px;background:rgba(255,255,255,.15)}
</style>
</head>
<body>

<header class="site-header">
  <div class="brand">
    <div class="brand-mark"></div>
    <div>
      <div class="brand-name">RV7</div>
      <div class="brand-tag">Rapid Vigil Field Operations Suite</div>
    </div>
  </div>
  <div class="login">LOGIN</div>
  <div class="search"></div>
  <nav class="main-nav">
    <span class="active">HOME</span><span>ABOUT US</span><span>SERVICES</span><span>APPLICATION</span><span>WHY RV7</span><span style="margin-right:0">CONTACT US</span>
  </nav>
</header>

<section class="hero" role="img" aria-label="Photo of two business people shaking hands in a modern office">
  <h1>Rapid Vigil - Field Operations<br>&amp; Coordination</h1>
  <div class="dots"><i></i><i></i><i></i><i></i></div>
</section>

<p class="intro">The product is focused on Preparing for an incident using Volunteer and Resource management and then responding to an incident with</p>
<div class="feature-band"></div>
<div class="feature" style="left:80px"><div class="photo" role="img" aria-label="Photo of incident management binders" style="background:linear-gradient(135deg,#c9b8c8,#6f5a78)"></div><h3>INCIDENT<br>MANAGEMENT</h3></div>
<div class="feature" style="left:351px"><div class="photo" role="img" aria-label="Photo of a smiling team of colleagues" style="background:linear-gradient(135deg,#e9e4de,#a89a8c)"></div><h3>TEAM<br>MANAGEMENT</h3></div>
<div class="feature" style="left:620px"><div class="photo" role="img" aria-label="Photo of people working at a laptop" style="background:linear-gradient(135deg,#8a8a8e,#2f3036)"></div><h3>TASK<br>MANAGEMENT</h3></div>
<div class="feature" style="left:889px"><div class="photo" role="img" aria-label="Photo of a team meeting around a table" style="background:linear-gradient(135deg,#c7b6a6,#5b4b42)"></div><h3>COMMUNICATION<br>MANAGEMENT</h3></div>

<section class="app-section">
  <div class="app-copy">
    <h2 class="section-title">APPLICATION</h2>
    <p>Once a situation is handled, the application provides complete reporting on each of the above aspects.</p>
    <p>RV7 offers a web based and mobile interface to assist the CERT Community.</p>
    <p>The roles from CERT teams have been created to have access to either the web, mobile or both the interfaces</p>
    <span class="btn">LEARN MORE</span>
  </div>

  <div class="phone" style="left:368px">
    <div class="status"></div>
    <div class="drawer-shade"></div>
    <div class="drawer">
      <div class="avatar"></div>
      <div class="who">Dana Mercer</div>
      <div class="role">Volunteer</div>
      <ul>
        <li>Dashboard</li><li class="on">Notifications</li><li>Profile</li><li>TODO List</li><li>Directory</li><li>Help</li><li>Share</li><li>Logout</li>
      </ul>
    </div>
  </div>

  <div class="phone" style="left:632px">
    <div class="status"></div>
    <div class="appbar">Notifications</div>
    <div class="card"><b>Impending Weather Conditions</b>Impending Weather Conditions</div>
    <div class="card"><b>Incoming Storms. Wrap up in 10 min</b>Incoming Storms. Wrap up in 10 min</div>
  </div>

  <div class="phone" style="left:891px">
    <div class="status"></div>
    <div class="appbar">TODO List</div>
    <div class="card"><b>Route Task</b>Supply Distribution<br>Unnamed Road, Pine Ridge, AZ 85000<div class="time">23 Min</div><div class="date">Apr 28, 2016 08:29 AM</div></div>
    <div class="card"><b>Find damage areas</b>Damage Assessment<br>Unnamed Rd, Riverbend Valley<div class="time">40 Min</div><div class="date">May 10, 2016 01:36 AM</div></div>
    <div class="card"><b>Supply Food</b>Supply Distribution<br>1200 Elm Hollow Rd, Fairview<div class="time">40 Min</div><div class="date">Jul 11, 2016 07:10 PM</div></div>
  </div>
</section>

<section class="why">
  <svg class="why-art" width="1200" height="454" viewBox="0 0 1200 454">
    <defs>
      <linearGradient id="sky" x1="0" y1="0" x2="0" y2="1">
        <stop offset="0" stop-color="#3f86d6"/><stop offset="1" stop-color="#bcd9f2"/>
      </linearGradient>
    </defs>
    <polygon points="677,0 1200,0 1200,454 544,454" fill="url(#sky)" role="img" aria-label="Photo of green road signs reading change and same against a cloudy sky"/>
  </svg>
  <h2>WHY ADOPT RV7</h2>
  <ul>
    <li>Easy system to register volunteers</li>
    <li>Accurate identification of number of CERT Volunteers available to help in an incident</li>
    <li>Efficient Communication mechanism to reach out to the volunteers via SMS</li>
    <li>Rich graphical visualization of Incidents &amp; Damages associated with the incidents</li>
    <li>Easy Management and Tracking of resources associated with</li>
  </ul>
  <span class="btn">LEARN MORE</span>
</section>

<section class="partners">
  <h4>PROUDLY FEATURED ON:</h4>
  <div class="partner" style="left:168px"><i></i>Northgate</div>
  <div class="partner" style="left:347px">Keystone</div>
  <div class="partner" style="left:525px">Harborline</div>
  <div class="partner" style="left:706px">Bluefield</div>
  <div class="partner" style="left:874px">Summit Co</div>
  <div class="partner" style="left:1040px">Alder</div>
</section>

<footer class="site-footer">
  <div class="foot-mark"></div>
  <p class="foot-about">The product is focused on Preparing for an incident using Volunteer and Resource management and then responding</p>
  <div class="btn-ghost">LEARN MORE</div>

  <div class="col" style="left:408px">
    <h5>QUICK LINKS</h5>
    <ul class="links"><li>Home</li><li>About Us</li><li>Services</li><li>Application</li><li>Why RV7</li><li>Contact Us</li></ul>
  </div>
  <div class="col" style="left:656px">
    <h5>GET SOCIAL</h5>
    <ul class="social"><li>Social Feed</li><li>Microposts</li><li>Video Channel</li><li>Pro Network</li></ul>
  </div>
  <div class="col" style="left:884px">
    <h5>GET IN TOUCH</h5>
    <div class="field">Enter Name</div>
    <div class="field">Enter Email</div>
    <div class="send">SEND</div>
  </div>
  <div class="foot-rule"></div>
  <p class="copyright">Company Name © 2016 | All Rights Reserved</p>
</footer>

</body>
</html>
```